Media Services Start-up -- Corporate Website and Logo Design. Inspiration required!

We need a logo design and corporate website design, including coding, for our start-up business.
Vennatra’s value proposition is based on bringing together media content from a vast number of geographies globally, adding human and AI curation, translation and editing, and delivering the content using tailored customer interfaces. On the one hand, the business brings together media coverage from all over the world, and on the other it brings together content, human skills and technology to deliver a supreme customer experience.
Vennatra is a B2B media monitoring and analytics business with emphasis on global customers. Vennatra's service offering is centred around sourcing media content from different markets, processing, storing and delivering the content and insights derived from it using an online platform / mobile app.
The messaging we want to create through the logo is:
- Global scope
- Speed of delivery
- Cost-efficiency
- Multi-lingual
- Tailor-made
- Trustworthy
Target Market(s)
Business to business, PR / Communications, Media, Marketing
Logo Text
Vennatra
Coding
Coded - Design and coding required
Number of Pages Required
5+ page
Font styles to use
Other font styles liked:
- See Design Brief for details
Colors
Designer to choose colors to be used in the design.

```html
<!DOCTYPE html>
<html lang="en">
<head>
<meta charset="utf-8">
<title>Vennatra — Global Media Intelligence</title>
<link rel="stylesheet" href="https://fonts.googleapis.com/css2?family=Saira+Condensed:wght@600;700&family=Roboto:wght@400;500;700&display=swap">
<style>
:root{
  --blue:#1a5ce0;
  --blue-dark:#1449b8;
  --ink:#1b1b1b;
  --text:#666a70;
  --white:#ffffff;
  --canvas:#eef1f6;
  --footer:#161616;
}
*{box-sizing:border-box;margin:0;padding:0}
html,body{width:1200px;height:4839px;overflow:hidden}
body{background:var(--canvas);font-family:Roboto,Arial,sans-serif;position:relative}
.page{position:absolute;left:98px;width:1004px;background:var(--white);box-shadow:0 10px 30px rgba(0,0,0,.12);overflow:hidden}
.page--home{top:494px;height:629px}
.page--solutions{top:1198px;height:3146px}
.topbar{height:40px;background:var(--blue);color:var(--white);font-size:13px;font-weight:500;position:relative}
.topbar__call{position:absolute;left:528px;top:12px;display:flex;align-items:center;gap:8px}
.topbar__signin{position:absolute;left:877px;top:12px}
.nav{height:46px;position:relative;border-bottom:1px solid #e5e5e5}
.logo{position:absolute;left:75px;top:4px;font-family:"Saira Condensed",sans-serif;font-weight:600;font-size:38px;letter-spacing:1px;color:var(--ink);line-height:40px}
.nav__menu{position:absolute;left:295px;top:16px;display:flex;gap:33px;list-style:none;font-size:12.5px;font-weight:500;color:var(--ink)}
.nav__menu .is-active{color:var(--blue)}
.hero{position:absolute;top:86px;left:0;width:1004px;height:543px;background:linear-gradient(100deg,#1b2230 0%,#2d3544 35%,#4a3a26 60%,#27303f 100%)}
.hero__title{position:absolute;left:75px;top:130px;font-family:"Saira Condensed",sans-serif;font-weight:700;font-size:42px;line-height:46px;letter-spacing:2px;color:var(--white)}
.hero__lead{position:absolute;left:75px;top:246px;width:500px;font-size:14px;font-weight:500;line-height:24px;color:var(--white)}
.lead-form{position:absolute;left:603px;top:71px;width:325px;height:325px;background:rgba(20,22,28,.88);border-radius:26px 26px 0 0;padding:28px 20px 0}
.lead-form__title{font-family:"Saira Condensed",sans-serif;font-weight:700;font-size:17px;letter-spacing:1.5px;color:var(--white);text-align:center;margin-bottom:20px}
.lead-form__field{height:40px;background:var(--white);margin-bottom:13px;font-size:13px;color:#777;padding:12px 12px}
.lead-form__button{height:42px;background:var(--blue);color:var(--white);font-size:14px;font-weight:500;text-align:center;line-height:42px}
.copyright{position:absolute;bottom:18px;left:387px;font-size:10px;color:var(--white)}
.banner{position:absolute;top:86px;left:0;width:1004px;height:304px;background:linear-gradient(90deg,#2a3140 0%,#3d4555 45%,#1f3760 70%,#8a4a2a 100%)}
.banner__title{position:absolute;left:0;right:0;top:118px;text-align:center;font-family:"Saira Condensed",sans-serif;font-weight:700;font-size:58px;letter-spacing:3px;color:var(--white)}
.service__media{position:absolute;width:454px;height:404px}
.service__media--left{left:0}
.service__media--right{left:550px}
.service__body{position:absolute;width:470px}
.service__title{font-family:"Saira Condensed",sans-serif;font-weight:700;font-size:29px;letter-spacing:1.5px;color:var(--ink);margin-bottom:12px}
.service__intro{font-size:13px;font-weight:500;color:var(--blue);line-height:23px;margin-bottom:14px}
.ticks{list-style:none}
.ticks li{position:relative;padding-left:25px;font-size:12.5px;line-height:25.5px;color:var(--text)}
.ticks li::before{content:"";position:absolute;left:0;top:7px;width:11px;height:11px;border-radius:50%;background:var(--blue)}
.ticks li::after{content:"";position:absolute;left:3.5px;top:9.5px;width:3px;height:5px;border:solid var(--white);border-width:0 1.5px 1.5px 0;transform:rotate(45deg)}
.site-footer{position:absolute;left:0;bottom:0;width:1004px;height:210px;background:var(--footer);color:var(--white)}
.site-footer .logo{color:var(--white);top:72px}
.site-footer__rule{position:absolute;left:296px;top:80px;width:2px;height:40px;background:var(--white)}
.site-footer__text{position:absolute;left:320px;top:82px;font-size:12px;line-height:20px}
.social{position:absolute;left:773px;top:86px;display:flex;gap:13px}
.social span{width:29px;height:29px;border-radius:50%;background:var(--white)}
.site-footer .copyright{bottom:14px}
</style>
</head>
<body>

<section class="page page--home">
  <div class="topbar">
    <div class="topbar__call">
      <svg width="13" height="13" viewBox="0 0 24 24" aria-hidden="true"><path fill="#fff" d="M6.6 10.8a15.1 15.1 0 0 0 6.6 6.6l2.2-2.2c.3-.3.7-.4 1-.2 1.1.4 2.3.6 3.6.6.6 0 1 .4 1 1V20c0 .6-.4 1-1 1A17 17 0 0 1 3 4c0-.6.4-1 1-1h3.5c.6 0 1 .4 1 1 0 1.3.2 2.5.6 3.6.1.3 0 .7-.2 1z"/></svg>
      CALL US TODAY : +1 555 010 4785
    </div>
    <div class="topbar__signin">SIGN IN</div>
  </div>
  <nav class="nav">
    <div class="logo">VENNATRA</div>
    <ul class="nav__menu"><li>HOME</li><li>SOLUTIONS</li><li>HOW WE DO IT</li><li>OUR PEOPLE</li><li>OUR TECHNOLOGY</li><li>CONTACT US</li></ul>
  </nav>
  <div class="hero" role="img" aria-label="Photo of a media analyst working at several monitors in a dim office">
    <h1 class="hero__title">DELIVERING GLOBAL MEDIA<br>INTELLIGENCE</h1>
    <p class="hero__lead">Vennatra is an international media intelligence service provider. We help communications teams build and operate truly global media monitoring and measurement programmes.</p>
    <form class="lead-form">
      <div class="lead-form__title">LEARN MORE ABOUT VENNATRA</div>
      <div class="lead-form__field">Name</div>
      <div class="lead-form__field">Email</div>
      <div class="lead-form__field">Phone</div>
      <div class="lead-form__button">Get Started</div>
    </form>
    <div class="copyright">© Copyrights.2019.Vennatra.All Rights Reserved</div>
  </div>
</section>

<section class="page page--solutions">
  <div class="topbar">
    <div class="topbar__call">
      <svg width="13" height="13" viewBox="0 0 24 24" aria-hidden="true"><path fill="#fff" d="M6.6 10.8a15.1 15.1 0 0 0 6.6 6.6l2.2-2.2c.3-.3.7-.4 1-.2 1.1.4 2.3.6 3.6.6.6 0 1 .4 1 1V20c0 .6-.4 1-1 1A17 17 0 0 1 3 4c0-.6.4-1 1-1h3.5c.6 0 1 .4 1 1 0 1.3.2 2.5.6 3.6.1.3 0 .7-.2 1z"/></svg>
      CALL US TODAY : +1 555 010 4785
    </div>
    <div class="topbar__signin">SIGN IN</div>
  </div>
  <nav class="nav">
    <div class="logo">VENNATRA</div>
    <ul class="nav__menu"><li>HOME</li><li class="is-active">SOLUTIONS</li><li>HOW WE DO IT</li><li>OUR PEOPLE</li><li>OUR TECHNOLOGY</li><li>CONTACT US</li></ul>
  </nav>
  <div class="banner" role="img" aria-label="Photo of an editor at a desk with video editing screens">
    <div class="banner__title">SOLUTIONS</div>
  </div>

  <svg class="service__media service__media--left" style="top:494px" viewBox="0 0 454 404" role="img" aria-label="Illustration of a global network of connected people icons">
    <defs><linearGradient id="gSource" x1="0" y1="0" x2="1" y2="1"><stop offset="0" stop-color="#2f5f74"/><stop offset=".5" stop-color="#8fa9a6"/><stop offset="1" stop-color="#c29a4e"/></linearGradient></defs>
    <path d="M0 0H414Q454 0 454 40V340Q454 370 424 372L0 404Z" fill="url(#gSource)"/>
  </svg>
  <div class="service__body" style="left:466px;top:526px">
    <h2 class="service__title">SOURCING</h2>
    <p class="service__intro">We help you build a content strategy that meets your budget and coverage needs across earned media - Print, Online, TV and Radio.</p>
    <ul class="ticks">
      <li>Identify geographies and markets of interest</li>
      <li>Build target media source lists to fulfil monitoring and measurement requirements</li>
      <li>Using our transparent cost calculator, we help you with accurate budgeting and planning to ensure you meet your strategy and objectives</li>
      <li>Translate and localise keyword searches and editorial instructions into efficient source-/ country-/ provider-specific needs to minimise wasted content.</li>
    </ul>
  </div>

  <svg class="service__media service__media--right" style="top:954px" viewBox="0 0 454 404" role="img" aria-label="Photo of a young man with headphones working on a laptop in an office">
    <defs><linearGradient id="gCollect" x1="0" y1="0" x2="1" y2="1"><stop offset="0" stop-color="#c9d3dc"/><stop offset=".5" stop-color="#6d7a86"/><stop offset="1" stop-color="#2b3440"/></linearGradient></defs>
    <path d="M0 0H454V404L30 340Q0 336 0 306Z" fill="url(#gCollect)"/>
  </svg>
  <div class="service__body" style="left:75px;top:1120px">
    <h2 class="service__title">COLLECTION</h2>
    <ul class="ticks">
      <li>We consolidate and manage the delivery of your global media content into a Cloud-based scalable media platform, taking the headache of content management away from your teams.</li>
    </ul>
  </div>

  <svg class="service__media service__media--left" style="top:1449px" viewBox="0 0 454 404" role="img" aria-label="Illustration of a glowing digital globe above an open hand">
    <defs><linearGradient id="gAug" x1="0" y1="0" x2="1" y2="1"><stop offset="0" stop-color="#0d2f5a"/><stop offset=".5" stop-color="#3a8fd0"/><stop offset="1" stop-color="#0a1f3d"/></linearGradient></defs>
    <path d="M0 0H414Q454 0 454 40V340Q454 370 424 372L0 404Z" fill="url(#gAug)"/>
  </svg>
  <div class="service__body" style="left:472px;top:1475px">
    <h2 class="service__title">AUGMENTATION</h2>
    <ul class="ticks">
      <li>We manage and normalise all of the source-level reference data - country, language, reach etc.</li>
      <li>We add editorial validation to ensure only the content required reaches your delivery, removing inevitable noise from source providers</li>
      <li>Tagging - AI and human based tagging to detect locations, people, topics, products, brands, services, etc.</li>
      <li>Human and automated grouping of stories across geographies - clustering, "also-in" groupings etc.</li>
      <li>Translation summarisation - AI Translation or human-created depending on budget, speed of delivery and need.</li>
      <li>Digest authoring - refining the essence of today's coverage into a concise board-ready output for your organisation</li>
    </ul>
  </div>

  <svg class="service__media service__media--right" style="top:1911px" viewBox="0 0 454 404" role="img" aria-label="Photo of two colleagues reviewing work at a computer">
    <defs><linearGradient id="gDeliver" x1="0" y1="0" x2="1" y2="1"><stop offset="0" stop-color="#2c3a4e"/><stop offset=".5" stop-color="#5a6a7c"/><stop offset="1" stop-color="#1c2633"/></linearGradient></defs>
    <path d="M0 0H454V404L30 340Q0 336 0 306Z" fill="url(#gDeliver)"/>
  </svg>
  <div class="service__body" style="left:75px;top:2040px;width:470px">
    <h2 class="service__title">DELIVERY</h2>
    <p class="service__intro">Early morning delivery of a consolidated, ready-to-consume media coverage</p>
    <ul class="ticks">
      <li>Customised email templates, delivering content in templates designed to meet your needs</li>
      <li>Customised platform - modern portal tailored to meet your media management needs, removing the unwanted clutter and focusing on the job at hand</li>
      <li>Integration with Intranets, third-party communication tools e.g. Chatwell, RSS readers, customised APIs</li>
    </ul>
  </div>

  <svg class="service__media service__media--left" style="top:2406px" viewBox="0 0 454 404" role="img" aria-label="Illustration of hands holding a tablet with colourful media icons flying out">
    <defs><linearGradient id="gInsight" x1="0" y1="0" x2="1" y2="1"><stop offset="0" stop-color="#d9dde3"/><stop offset=".5" stop-color="#6b8fb8"/><stop offset="1" stop-color="#b8794f"/></linearGradient></defs>
    <path d="M0 0H414Q454 0 454 40V340Q454 370 424 372L0 404Z" fill="url(#gInsight)"/>
  </svg>
  <div class="service__body" style="left:466px;top:2447px">
    <h2 class="service__title">MEDIA INSIGHTS &amp; CONSULTANCY</h2>
    <p class="service__intro">We help you build a content strategy that meets your budget and coverage needs across earned media - Print, Online, TV and Radio.</p>
    <ul class="ticks">
      <li>Levering the normalised content sets from your integrated monitoring service, we can analyse and tag your coverage based on complex qualitative measurement criteria, consistent across all languages and geographies, to combine with quantitative metrics.</li>
      <li>Ability to create a single consistent measurement programme across all of your global operations.</li>
      <li>Consultancy to HQ and local offices on how to utilise and align existing measurement and insight initiatives to provide continuity.</li>
      <li>Customised online dashboards with near real time data insights, coupled with Board-ready offline reporting and export options.</li>
      <li>Integration with social media content, third-party data, point-of-sale, Metricly Analytics, and delivering on your Integrated Communications Framework</li>
    </ul>
  </div>

  <footer class="site-footer">
    <div class="logo">VENNATRA</div>
    <div class="site-footer__rule"></div>
    <p class="site-footer__text">Lorem ipsum dolor sit amet, consectetur adipiscing elit,<br>sed do eiusmod tempor incididunt ut labore et</p>
    <div class="social" aria-label="Social links"><span></span><span></span><span></span><span></span></div>
    <div class="copyright">© Copyrights.2019.Vennatra.All Rights Reserved</div>
  </footer>
</section>

</body>
</html>
```